Cool date project and tattoo

My children were born randomly on dates with a crazy number sequence and I am getting married on the next date in the sequence. The dates are as follows:

6/13/14
7/15/16
8/17/18
9/19/20.

I want a piece of art that has these dates beautifully drawn/written which I also would like to turn into a tattoo one day. I am not sure whether to add the kids names or not but would also be interested in seeing options. Here are the names of the kids and the wedding:

6/13/14 - Colby
7/15/16 - Fenna
8/17/18 - Mireth
9/19/20 - Wedding

I'd love to see options of how these dates could be presented in a unique and beautiful way!

I have not seen anything that I love yet..

Serif
Decorative
Script

• My project must have the dates included in the design
• I want to be able to see the dates relatively clearly, I want it to be able to not only be a large art project when printed on a large canvas, but also a cool looking tattoo.

Please check the color palates I added to see colors I like together.

```html
<!DOCTYPE html>
<html lang="en">
<head>
<meta charset="utf-8">
<title>Dates in Bloom</title>
<link rel="stylesheet" href="https://fonts.googleapis.com/css2?family=Stardos+Stencil:wght@400;700&display=swap">
<style>
  :root {
    --rose: #ee3e5f;
    --rose-light: #fbd6de;
    --ember: #e07a3a;
    --honey: #f2c94c;
    --lagoon: #3aa58f;
    --slate: #2c4a5a;
    --paper-top: #f1f1f2;
    --paper-bottom: #dcdddf;
  }
  * { margin: 0; padding: 0; box-sizing: border-box; }
  html, body { width: 1200px; height: 628px; overflow: hidden; }
  body {
    background: radial-gradient(ellipse at 50% 40%, var(--paper-top), var(--paper-bottom));
    font-family: "Stardos Stencil", Georgia, serif;
    position: relative;
  }
  .badge {
    position: absolute;
    top: 64px;
    width: 260px;
    height: 390px;
  }
  .badge svg { width: 100%; height: 100%; display: block; overflow: visible; }
  .badge--colby   { left: 38px; }
  .badge--fenna   { left: 316px; }
  .badge--mireth  { left: 594px; }
  .badge--wedding { left: 872px; }

  .rose-art { fill: url(#roseTone); }
  .ribbon { stroke: var(--slate); stroke-width: 3; stroke-linejoin: round; }
  .ribbon--name { fill: var(--lagoon); }
  .ribbon--days { fill: var(--ember); }
  .month-box { fill: var(--honey); stroke: var(--slate); stroke-width: 3; }
  .ribbon-fold { fill: none; stroke: var(--slate); stroke-width: 2; opacity: .6; }
  .badge-text {
    fill: var(--slate);
    font-family: "Stardos Stencil", Georgia, serif;
    font-weight: 700;
    text-anchor: middle;
  }
  .badge-text--name { font-size: 36px; }
  .badge-text--month { font-size: 44px; }
  .badge-text--day { font-size: 44px; }

  .palette {
    position: absolute;
    left: 1122px;
    top: 477px;
    width: 66px;
    height: 138px;
    display: flex;
    flex-direction: column;
  }
  .palette span {
    flex: 1;
    display: flex;
    align-items: center;
    justify-content: center;
    font-family: Arial, sans-serif;
    font-size: 5px;
    letter-spacing: 1px;
    text-transform: uppercase;
    color: #fff;
  }
  .palette .swatch-rose   { background: var(--rose); }
  .palette .swatch-ember  { background: var(--ember); }
  .palette .swatch-honey  { background: var(--honey); }
  .palette .swatch-lagoon { background: var(--lagoon); }
  .palette .swatch-slate  { background: var(--slate); }
</style>
</head>
<body>

<svg width="0" height="0" style="position:absolute" aria-hidden="true">
  <defs>
    <radialGradient id="roseTone" cx="50%" cy="45%" r="60%">
      <stop offset="0%" stop-color="#fbd6de"/>
      <stop offset="100%" stop-color="#f27a92"/>
    </radialGradient>
    <g id="badgeFrame">
      <path class="rose-art" role="img" aria-label="Illustrated rose with leaves behind the ribbons"
            d="M40,40 C70,0 190,0 220,40 C250,80 250,140 240,180 C260,230 250,300 225,340 C200,380 60,380 35,340 C10,300 0,230 20,180 C10,140 10,80 40,40 Z"/>
      <rect class="month-box" x="85" y="173" width="90" height="78"/>
      <path class="ribbon ribbon--name"
            d="M6,118 C60,100 110,138 160,118 C200,102 230,104 254,98 L248,140 L254,166 C226,170 202,166 162,184 C112,206 62,168 6,186 L14,152 Z"/>
      <path class="ribbon ribbon--days"
            d="M6,238 C60,220 110,256 160,236 C200,220 230,222 254,216 L248,262 L254,290 C226,294 202,290 162,308 C112,330 62,292 6,312 L14,276 Z"/>
      <path class="ribbon-fold" d="M130,246 L130,318"/>
    </g>
  </defs>
</svg>

<section class="badge badge--colby" aria-label="Colby, 6/13/14">
  <svg viewBox="0 0 260 390">
    <use href="#badgeFrame"/>
    <text class="badge-text badge-text--name" x="130" y="156">Colby</text>
    <text class="badge-text badge-text--month" x="130" y="228">6</text>
    <text class="badge-text badge-text--day" x="72" y="284">13</text>
    <text class="badge-text badge-text--day" x="190" y="282">14</text>
  </svg>
</section>

<section class="badge badge--fenna" aria-label="Fenna, 7/15/16">
  <svg viewBox="0 0 260 390">
    <use href="#badgeFrame"/>
    <text class="badge-text badge-text--name" x="130" y="156">Fenna</text>
    <text class="badge-text badge-text--month" x="130" y="228">7</text>
    <text class="badge-text badge-text--day" x="72" y="284">15</text>
    <text class="badge-text badge-text--day" x="190" y="282">16</text>
  </svg>
</section>

<section class="badge badge--mireth" aria-label="Mireth, 8/17/18">
  <svg viewBox="0 0 260 390">
    <use href="#badgeFrame"/>
    <text class="badge-text badge-text--name" x="130" y="156">Mireth</text>
    <text class="badge-text badge-text--month" x="130" y="228">8</text>
    <text class="badge-text badge-text--day" x="72" y="284">17</text>
    <text class="badge-text badge-text--day" x="190" y="282">18</text>
  </svg>
</section>

<section class="badge badge--wedding" aria-label="Wedding, 9/19/20">
  <svg viewBox="0 0 260 390">
    <use href="#badgeFrame"/>
    <text class="badge-text badge-text--name" x="130" y="156">Wedding</text>
    <text class="badge-text badge-text--month" x="130" y="228">9</text>
    <text class="badge-text badge-text--day" x="72" y="284">19</text>
    <text class="badge-text badge-text--day" x="190" y="282">20</text>
  </svg>
</section>

<aside class="palette" aria-label="Colour palette">
  <span class="swatch-rose">rose</span>
  <span class="swatch-ember">ember</span>
  <span class="swatch-honey">honey</span>
  <span class="swatch-lagoon">lagoon</span>
  <span class="swatch-slate">slate</span>
</aside>

</body>
</html>
```